New Business Card Design for Manufacturing

We are an engineering/manufacturing company that offers Advanced machining/assembly/engineering services, as well as innovative products for the heavy duty engine cooling markets.

We are looking to get a new business card designed that is clean and modern looking, but still fits the wide range of technical/skilled work we do.

- We hope to use this design as the base for other design work in new Presentations, web, and print work.

Industry/Entity Type

Engineering

Contact Information for Business Card

Our preferred color of blue is (RGB) 22/71/159 but can vary slightly from that color. Our content will be our Logo and full company name (Vantrell Forge Works, Inc.), company address, name, job title, phone number with extension, cell number, fax number, website, and email address on the cards.
We'd like the full company name next to the logo, but we are open to other interpretations of that layout.
Preferably, we would like the back side to be clean with just our logo, and the front to contain all of the contact information.

Colors
2f74b4
0355a3
85abd2

Requirements
Must have
• - Logo, company name, needed content - We are open to interpretation beyond that.
• - Standard size business card.
• - Horizontal orientation.
• - Enough space for lengthy names / job titles (for example, a job title could read "Directory of Human Resources" or "V.P. of Governmental Affairs"). We need this to look clean, whether the title be short (CEO) or long (as described above).

```html
<!DOCTYPE html>
<html lang="en">
<head>
<meta charset="utf-8">
<title>Vantrell Forge Works – Business Card</title>
<link rel="stylesheet" href="https://fonts.googleapis.com/css2?family=Open+Sans:wght@400;600;700;800&display=swap">
<style>
  :root {
    --page-bg: #e4e4e4;
    --card-black: #0b0c0e;
    --card-white: #f4f4f4;
    --brand-blue: #0355a3;
    --swoosh-gray: #7d8690;
    --text-dark: #3a3d42;
    --tagline-gray: #7a7f86;
    --white: #ffffff;
  }
  * { box-sizing: border-box; margin: 0; padding: 0; }
  html, body {
    width: 1200px; height: 576px; overflow: hidden;
    background: var(--page-bg);
    font-family: "Open Sans", Arial, sans-serif;
  }
  .card {
    position: absolute; top: 138px;
    width: 484px; height: 294px;
    border-radius: 13px; overflow: hidden;
  }
  .card-back { left: 82px; background: var(--card-black); }
  .card-front { left: 602px; width: 480px; height: 292px; background: var(--card-white); }

  .back-brand {
    position: absolute; left: 0; right: 0; top: 112px;
    text-align: center;
  }
  .back-brand .brand-name {
    font-size: 34px; font-weight: 800; color: var(--white); line-height: 1.2;
  }
  .tagline {
    font-weight: 700; text-transform: uppercase; color: var(--tagline-gray);
    letter-spacing: 0.5px; line-height: 1.2;
  }
  .back-brand .tagline { font-size: 17px; margin-top: 12px; }

  .front-wave { position: absolute; left: 0; top: 0; width: 480px; height: 130px; }
  .holder { position: absolute; right: 22px; top: 18px; text-align: right; color: var(--white); }
  .holder-name { font-size: 21px; font-weight: 600; line-height: 1.2; }
  .holder-title { font-size: 12px; margin-top: 3px; }

  .front-brand { position: absolute; left: 24px; top: 112px; }
  .front-brand .brand-name { font-size: 27px; font-weight: 800; color: var(--brand-blue); line-height: 1.2; }
  .front-brand .tagline { font-size: 14px; margin-top: 6px; }

  .address {
    position: absolute; left: 22px; top: 218px;
    font-size: 12.5px; line-height: 17.5px; color: var(--text-dark);
  }
  .address .web { color: var(--brand-blue); }
  .contacts {
    position: absolute; right: 14px; top: 200px; list-style: none;
    font-size: 12.5px; line-height: 17.5px; color: var(--text-dark);
  }
  .contacts li { display: flex; justify-content: flex-end; align-items: center; gap: 6px; }
  .contacts svg { width: 11px; height: 11px; fill: var(--brand-blue); flex: none; }
</style>
</head>
<body>
  <section class="card card-back" aria-label="Card back">
    <div class="back-brand">
      <div class="brand-name">Vantrell Forge Works</div>
      <div class="tagline">Engineering Tomorrow</div>
    </div>
  </section>

  <section class="card card-front" aria-label="Card front">
    <svg class="front-wave" viewBox="0 0 480 130" aria-hidden="true">
      <path fill="var(--brand-blue)" d="M0,0 H480 V94 C420,92 360,70 290,44 C210,16 110,6 0,28 Z"/>
      <path fill="var(--swoosh-gray)" d="M0,56 C80,32 175,28 255,48 C335,68 400,98 480,104 V118 C400,112 330,86 250,64 C170,46 80,50 0,78 Z"/>
      <path fill="var(--swoosh-gray)" d="M40,44 C120,24 200,20 262,34 C200,28 120,32 40,48 Z"/>
    </svg>
    <div class="holder">
      <div class="holder-name">John Doe Smith</div>
      <div class="holder-title">Managing Director</div>
    </div>

    <div class="front-brand">
      <div class="brand-name">Vantrell Forge Works</div>
      <div class="tagline">Engineering Tomorrow</div>
    </div>

    <div class="address">
      <div>234 Anywhere St., Any City,</div>
      <div>Any Town, US 123456</div>
      <div class="web">www.yourwebsite.com</div>
    </div>

    <ul class="contacts">
      <li>111-2222-2222 (VFW)
        <svg viewBox="0 0 12 12" aria-label="Phone"><path d="M1,4 C1,2 3,1 6,1 C9,1 11,2 11,4 L9,5 L8,3.5 L4,3.5 L3,5 Z M3,6 H9 L10,11 H2 Z"/></svg></li>
      <li>333-3333-3333
        <svg viewBox="0 0 12 12" aria-label="Mobile"><path d="M3,0.5 H9 V11.5 H3 Z M4,2 V9 H8 V2 Z"/></svg></li>
      <li>444-4444-4444
        <svg viewBox="0 0 12 12" aria-label="Fax"><path d="M3,1 H9 V4 H3 Z M1,4.5 H11 V9 H9 V7 H3 V9 H1 Z M3,7.5 H9 V11 H3 Z"/></svg></li>
      <li>johndoe@yourwebsite.com
        <svg viewBox="0 0 12 12" aria-label="Email"><path d="M0.5,2.5 H11.5 V9.5 H0.5 Z M1.5,3.3 L6,6.8 L10.5,3.3 V3 H1.5 Z" fill-rule="evenodd"/></svg></li>
    </ul>
  </section>
</body>
</html>
```